Business Card for Health Food Store

I need a business card for a health food store that includes the following information.

=========
FRONT
=========

***White background***

Bright Harvest (logo)
Supplements - Health Foods - Remedies

2214 Alder Rd.
Willow Bend, CA 95412
(corner of Ferris Ln.)

707-482-3196

BrightHarvest.co
BrightHarvestGoods@mailbox-example.com

On the right side of the front of the card, use a circle type seal with 25 large in the middle. Put the dates below it.
"Celebrating 25 Years"
2001 - 2026

*DO NOT USE A PERSON'S NAME ON THE CARD*

==========
BACK
==========

***Green background***

Full logo in white along with the social logos and handles.

FB Logo / BrightHarvestShop
IG Logo / BrightHarvestShop
Twitter Logo / VisitBrightHarvest

When done I'll need the file in PSD and AI.

Target Market(s)

Surrounding local community

Industry/Entity Type

Retail Health Food Store

Contact Information for Business Card

See brief

Requirements
Must have
• Must be double-sided

```html
<!DOCTYPE html>
<html lang="en">
<head>
<meta charset="utf-8">
<title>Bright Harvest — Business Card</title>
<link href="https://fonts.googleapis.com/css2?family=Montserrat:wght@800&family=Oswald:wght@500&family=Open+Sans:wght@400;600&display=swap" rel="stylesheet">
<style>
  :root {
    --backdrop: #2b2b2b;
    --card-white: #ffffff;
    --brand-green: #4cb848;
    --ink: #111111;
  }
  * { box-sizing: border-box; margin: 0; padding: 0; }
  html, body { width: 1200px; height: 1200px; overflow: hidden; }
  body {
    background: var(--backdrop);
    font-family: "Open Sans", sans-serif;
    display: flex;
    justify-content: center;
    align-items: center;
    gap: 60px;
  }
  .card {
    width: 480px;
    height: 780px;
    border-radius: 40px;
    display: flex;
    flex-direction: column;
    align-items: center;
    text-align: center;
  }
  .card--front { background: var(--card-white); color: var(--ink); padding-top: 60px; }
  .card--back { background: var(--brand-green); color: var(--card-white); padding-top: 150px; }

  .brand { display: flex; flex-direction: column; align-items: center; }
  .brand__dot {
    width: 56px; height: 56px; border-radius: 50%;
    background: var(--brand-green);
    margin-bottom: 14px;
  }
  .card--back .brand__dot { background: var(--card-white); }
  .brand__name {
    font-family: "Montserrat", sans-serif;
    font-weight: 800;
    font-size: 50px;
    line-height: 1;
    letter-spacing: -0.5px;
  }
  .brand__tagline {
    font-family: "Oswald", sans-serif;
    font-weight: 500;
    font-size: 21px;
    letter-spacing: 1px;
    margin-top: 10px;
    color: var(--brand-green);
  }
  .card--back .brand__tagline { color: var(--card-white); }

  .seal {
    width: 200px; height: 200px; margin-top: 22px;
    border-radius: 50%;
    background: var(--brand-green);
    color: var(--card-white);
    display: flex; flex-direction: column; align-items: center; justify-content: center;
  }
  .seal__label { font-weight: 600; font-size: 14px; letter-spacing: 3px; }
  .seal__number { font-family: "Oswald", sans-serif; font-weight: 500; font-size: 80px; line-height: 1; }
  .seal__years { font-weight: 600; font-size: 11px; letter-spacing: 2px; }
  .seal__dates { font-weight: 600; font-size: 18px; margin-top: 4px; }

  .contact-icons {
    display: flex; align-items: center; gap: 12px;
    margin-top: 22px; width: 400px;
  }
  .rule { flex: 1; height: 2px; background: var(--brand-green); }
  .icon-box {
    width: 40px; height: 40px; border-radius: 7px;
    background: var(--brand-green);
    display: flex; align-items: center; justify-content: center;
  }
  .contact-lines { margin-top: 12px; font-size: 19px; line-height: 1.35; }
  .contact-lines .phone { font-size: 22px; }
  .divider { width: 400px; height: 2px; background: var(--brand-green); margin: 14px 0; }
  .address { font-size: 18px; line-height: 1.35; font-style: normal; }

  .socials { margin-top: 70px; display: flex; flex-direction: column; gap: 22px; list-style: none; }
  .social { display: flex; flex-direction: column; align-items: center; gap: 6px; font-size: 21px; }
  .social__badge {
    width: 32px; height: 32px; border-radius: 50%;
    border: 2px solid var(--card-white);
  }
</style>
</head>
<body>

<section class="card card--front" aria-label="Card front">
  <div class="brand">
    <span class="brand__dot"></span>
    <h1 class="brand__name">Bright Harvest</h1>
    <p class="brand__tagline">SUPPLEMENTS • HEALTH FOODS • REMEDIES</p>
  </div>

  <div class="seal" aria-label="Celebrating 25 years, 2001 to 2026">
    <span class="seal__label">CELEBRATING</span>
    <span class="seal__number">25</span>
    <span class="seal__years">YEARS</span>
    <span class="seal__dates">2001 - 2026</span>
  </div>

  <div class="contact-icons">
    <span class="rule"></span>
    <span class="icon-box" aria-label="Phone">
      <svg width="22" height="22" viewBox="0 0 24 24"><path d="M6.6 10.8a15 15 0 0 0 6.6 6.6l2.2-2.2a1 1 0 0 1 1-.25 11.4 11.4 0 0 0 3.6.6 1 1 0 0 1 1 1V20a1 1 0 0 1-1 1A17 17 0 0 1 3 4a1 1 0 0 1 1-1h3.5a1 1 0 0 1 1 1c0 1.25.2 2.45.6 3.6a1 1 0 0 1-.25 1z" fill="#fff"/></svg>
    </span>
    <span class="icon-box" aria-label="Email">
      <svg width="22" height="22" viewBox="0 0 24 24"><rect x="3" y="5" width="18" height="14" rx="1.5" fill="#fff"/><polyline points="3.5,6 12,13 20.5,6" fill="none" stroke="#4cb848" stroke-width="1.8"/></svg>
    </span>
    <span class="icon-box" aria-label="Website">
      <svg width="22" height="22" viewBox="0 0 24 24" fill="none" stroke="#fff" stroke-width="1.8"><circle cx="12" cy="12" r="9"/><ellipse cx="12" cy="12" rx="4" ry="9"/><line x1="3" y1="12" x2="21" y2="12"/></svg>
    </span>
    <span class="rule"></span>
  </div>

  <div class="contact-lines">
    <p class="phone">707-482-3196</p>
    <p>BrightHarvestGoods@mailbox-example.com</p>
    <p>www.BrightHarvest.co</p>
  </div>

  <span class="divider"></span>

  <address class="address">
    2214 Alder Rd.<br>
    Willow Bend, CA 95412<br>
    (corner of Ferris Ln.)
  </address>
</section>

<section class="card card--back" aria-label="Card back">
  <div class="brand">
    <span class="brand__dot"></span>
    <h2 class="brand__name">Bright Harvest</h2>
    <p class="brand__tagline">SUPPLEMENTS • HEALTH FOODS • REMEDIES</p>
  </div>

  <ul class="socials">
    <li class="social"><span class="social__badge"></span>BrightHarvestShop</li>
    <li class="social"><span class="social__badge"></span>BrightHarvestShop</li>
    <li class="social"><span class="social__badge"></span>VisitBrightHarvest</li>
  </ul>
</section>

</body>
</html>
```